Stylish Business Cards Wanted

- DOUBLE SIDED Design Required -

High end, edgy cards for a corporate and personal stylist. Must include logo,
Name: Belinda Harwick
Title: Director and Stylist
telephone : +61 8 7142 5809
email: belinda@theloombriefing.example
website: theloombriefing.example
Tag: Corporate Workwear & Uniform Specialist | Personal Stylist
Would like nice icons for telephone, email, website

Target Market(s)

Businesses wanting stylish uniforms, people wanting stylish wardrobes

Industry/Entity Type

Corporate Workwear Stylist

Contact Information for Business Card

I would like black, white and gold foiling incorporated in the design - possibly a touch of the other colours on my branding guide attached Name: Belinda Harwick Title: Director and Stylist telephone : +61 8 7142 5809 email: belinda@theloombriefing.example website: theloombriefing.example Tag: Corporate Workwear & Uniform Specialist | Personal Stylist Would like nice icons for telephone, email, website

Font styles to use
Other font styles liked:
• Raleway

Colors

Designer to choose colors to be used in the design.

Requirements
Must have
• Gold foil accents

```html
<!DOCTYPE html>
<html lang="en">
<head>
<meta charset="utf-8">
<title>The Loom Briefing – Business Card</title>
<link rel="stylesheet" href="https://fonts.googleapis.com/css2?family=Open+Sans:wght@400;600&display=swap">
<style>
  :root {
    --charcoal: #343334;
    --gold: #e4bf5c;
    --white: #ffffff;
    --backdrop: #ecebe8;
    --logo-ink: #2f2e2f;
  }
  html, body {
    margin: 0;
    width: 1200px;
    height: 900px;
    overflow: hidden;
    background: var(--backdrop);
    font-family: "Open Sans", Arial, sans-serif;
  }
  .card {
    position: absolute;
    left: 100px;
    top: 140px;
    width: 1000px;
    height: 620px;
    background: var(--charcoal);
    overflow: hidden;
    box-shadow: 0 12px 30px rgba(0,0,0,0.18);
  }
  .gold-panel {
    position: absolute;
    left: 675px;
    top: 0;
    width: 325px;
    height: 100%;
    background: var(--gold);
  }
  .logo-disc {
    position: absolute;
    left: 411px;
    top: 41px;
    width: 536px;
    height: 536px;
    border-radius: 50%;
    background: var(--white);
    display: flex;
    align-items: center;
    justify-content: center;
  }
  .brand-name {
    font-weight: 600;
    font-size: 34px;
    letter-spacing: 1px;
    color: var(--logo-ink);
  }
  .identity {
    position: absolute;
    left: 45px;
    top: 128px;
    color: var(--white);
  }
  .person-name {
    margin: 0;
    font-size: 25px;
    font-weight: 400;
    letter-spacing: 4px;
    color: var(--gold);
    text-transform: uppercase;
    line-height: 1.1;
  }
  .person-title {
    margin: 10px 0 0;
    font-size: 13.5px;
    line-height: 1.2;
  }
  .tagline {
    position: absolute;
    left: 45px;
    top: 222px;
    margin: 0;
    font-size: 17px;
    line-height: 24.5px;
    color: var(--white);
  }
  .contact-list {
    position: absolute;
    left: 45px;
    top: 349px;
    margin: 0;
    padding: 0;
    list-style: none;
    color: var(--white);
  }
  .contact-item {
    display: flex;
    align-items: center;
    height: 30px;
    margin-bottom: 8px;
    font-size: 19px;
  }
  .contact-item.web { font-size: 17px; }
  .contact-icon {
    width: 30px;
    height: 30px;
    margin-right: 18px;
    flex: none;
  }
</style>
</head>
<body>
  <section class="card" aria-label="Business card">
    <div class="gold-panel"></div>
    <div class="logo-disc">
      <span class="brand-name">The Loom Briefing</span>
    </div>

    <div class="identity">
      <h1 class="person-name">Belinda Harwick</h1>
      <p class="person-title">Director and Stylist</p>
    </div>

    <p class="tagline">
      Corporate Workwear &amp;<br>
      Uniform Specialist |<br>
      Personal Stylist
    </p>

    <ul class="contact-list">
      <li class="contact-item">
        <svg class="contact-icon" viewBox="0 0 30 30" aria-hidden="true">
          <rect width="30" height="30" rx="5" fill="var(--gold)"/>
          <path d="M9 7.5c1-.6 2 .1 2.6 1.1l1.3 2.3c.5.9.2 1.7-.6 2.3l-.8.6c.8 1.9 2.3 3.4 4.2 4.3l.7-.8c.6-.7 1.5-1 2.3-.5l2.3 1.3c1 .6 1.600 1.7 1 2.6-1 1.7-2.8 2.4-4.6 1.8C12.5 21 9 17.5 7.6 12.6 7 10.5 7.6 8.5 9 7.5z" fill="none" stroke="var(--charcoal)" stroke-width="1.6"/>
          <path d="M17 7.5a6 6 0 0 1 5.5 5.5M17 10.5a3 3 0 0 1 2.5 2.5" fill="none" stroke="var(--charcoal)" stroke-width="1.4" stroke-linecap="round"/>
        </svg>
        <span>+61 8 7142 5809</span>
      </li>
      <li class="contact-item">
        <svg class="contact-icon" viewBox="0 0 30 30" aria-hidden="true">
          <rect width="30" height="30" rx="5" fill="var(--gold)"/>
          <rect x="10" y="6" width="10" height="6" fill="none" stroke="var(--charcoal)" stroke-width="1.6"/>
          <rect x="6" y="12" width="18" height="9" rx="1.5" fill="none" stroke="var(--charcoal)" stroke-width="1.6"/>
          <rect x="10" y="17" width="10" height="8" fill="var(--gold)" stroke="var(--charcoal)" stroke-width="1.6"/>
          <path d="M12 20h6M12 22.5h6" stroke="var(--charcoal)" stroke-width="1.2"/>
        </svg>
        <span>+61 8 7142 5809</span>
      </li>
      <li class="contact-item">
        <svg class="contact-icon" viewBox="0 0 30 30" aria-hidden="true">
          <rect x="2" y="6" width="26" height="18" rx="1" fill="none" stroke="var(--gold)" stroke-width="1.8"/>
          <path d="M2.5 7l12.5 10 12.5-10M2.5 23.5l9.5-8.5M27.5 23.5l-9.5-8.5" fill="none" stroke="var(--gold)" stroke-width="1.8"/>
        </svg>
        <span>belinda@theloombriefing.example</span>
      </li>
      <li class="contact-item web">
        <svg class="contact-icon" viewBox="0 0 30 30" aria-hidden="true">
          <rect width="30" height="30" rx="5" fill="var(--gold)"/>
          <circle cx="15" cy="15" r="9" fill="none" stroke="var(--charcoal)" stroke-width="1.6"/>
          <ellipse cx="15" cy="15" rx="4" ry="9" fill="none" stroke="var(--charcoal)" stroke-width="1.4"/>
          <path d="M6 15h18M7.5 10.5h15M7.5 19.5h15" stroke="var(--charcoal)" stroke-width="1.4"/>
        </svg>
        <span>theloombriefing.example</span>
      </li>
    </ul>
  </section>
</body>
</html>
```